Fernhale Business Card Design

We are looking for a fresh business card design for our new logo. We would like a business card that is unique but friendly. We are in the window coverings business offering blinds, shutters and shades for homes.

Target Market(s)

Targeting the end-consumer

Industry/Entity Type

Business

Requirements
Must have
• Must have a dedicates space for a photo of our sales person. Must contain our new logo (attached).

```html
<!DOCTYPE html>
<html lang="en">
<head>
<meta charset="utf-8">
<title>Fernhale Business Card</title>
<link rel="stylesheet" href="https://fonts.googleapis.com/css2?family=Alegreya:wght@500&family=Montserrat:wght@300;400;600&display=swap">
<style>
  :root {
    --canvas: #e4e2df;
    --card-white: #ffffff;
    --card-black: #1c1c1c;
    --brand-green: #6cc12e;
    --band-grey: #5d5e62;
    --ink: #4a4b4f;
    --photo-light: #d8d6d4;
    --photo-dark: #3d3d40;
  }
  * { margin: 0; padding: 0; box-sizing: border-box; }
  html, body { width: 1200px; height: 715px; overflow: hidden; }
  body {
    background: var(--canvas);
    font-family: "Montserrat", Arial, sans-serif;
    position: relative;
  }
  .card {
    position: absolute;
    top: 202px;
    width: 540px;
    height: 310px;
    box-shadow: 0 6px 18px rgba(0,0,0,0.18);
    overflow: hidden;
  }
  .card-back {
    left: 40px;
    background: var(--card-black);
    border-bottom: 4px solid var(--brand-green);
  }
  .card-front { left: 620px; background: var(--card-white); }

  .brand {
    position: absolute;
    display: flex;
    align-items: center;
    gap: 14px;
    font-family: "Alegreya", Georgia, serif;
    font-weight: 500;
    letter-spacing: 0.5px;
  }
  .brand-square {
    width: 40px; height: 40px;
    background: var(--brand-green);
  }
  .card-back .brand { left: 60px; top: 100px; color: #ffffff; font-size: 60px; }
  .card-back .brand-square { width: 56px; height: 56px; }
  .card-front .brand { right: 30px; top: 60px; color: var(--ink); font-size: 40px; }

  .photo-area {
    position: absolute;
    left: 30px; top: 18px;
    width: 210px; height: 212px;
    background: linear-gradient(180deg, var(--photo-light) 0%, var(--photo-dark) 70%);
  }
  .name-band {
    position: absolute;
    left: 0; top: 222px;
    width: 275px; height: 26px;
    background: var(--brand-green);
    color: #fff;
    display: flex; align-items: center;
    padding-left: 28px;
    font-size: 13px;
    letter-spacing: 0.5px;
  }
  .name-band .person { font-weight: 600; margin-right: 8px; }
  .name-band .role { font-weight: 300; font-size: 11px; }
  .handle-band {
    position: absolute;
    left: 275px; right: 0; top: 252px;
    height: 24px;
    background: var(--band-grey);
    color: #fff;
    font-size: 11px;
    text-align: right;
    padding-right: 28px;
    line-height: 24px;
    letter-spacing: 0.5px;
  }
  .contact {
    position: absolute;
    right: 28px; top: 128px;
    color: var(--ink);
    font-size: 11px;
    line-height: 15px;
    text-align: right;
  }
  .address { margin-bottom: 6px; }
  .contact-line { display: flex; justify-content: flex-end; align-items: center; gap: 10px; }
  .contact-line svg { width: 10px; height: 10px; fill: var(--brand-green); flex: none; }
</style>
</head>
<body>
  <section class="card card-back">
    <div class="brand"><span class="brand-square"></span>Fernhale</div>
  </section>

  <section class="card card-front">
    <div class="photo-area" role="img" aria-label="Portrait photo of the sales person"></div>
    <div class="name-band"><span class="person">DANA WHITFIELD</span><span class="role">REALTOR</span></div>
    <div class="handle-band">@fernhalehome</div>

    <div class="brand"><span class="brand-square"></span>Fernhale</div>

    <div class="contact">
      <p class="address">P.O.Box: 214,<br>Lindenport, Calvera</p>
      <p class="contact-line">(014) 552-3870
        <svg viewBox="0 0 10 10"><path d="M2 0.5 L3.8 2.6 L2.9 3.6 Q4 5.9 6.4 7.1 L7.4 6.2 L9.5 8 L8.3 9.5 Q2.5 8.5 0.5 1.7 Z"/></svg></p>
      <p class="contact-line">(014) 552-3871
        <svg viewBox="0 0 10 10"><path d="M2.5 0 H7.5 V10 H2.5 Z M3.3 1 V8 H6.7 V1 Z"/></svg></p>
      <p class="contact-line">(014) 552-3872
        <svg viewBox="0 0 10 10"><path d="M2.5 0 H7.5 V3 H10 V8 H0 V3 H2.5 Z M2 9 H8 V10 H2 Z"/></svg></p>
      <p class="contact-line">info@fernhalehome.com
        <svg viewBox="0 0 10 10"><path d="M0 2 H10 V8 H0 Z M0.8 2.6 L5 5.6 L9.2 2.6 Z" fill-rule="evenodd"/></svg></p>
      <p class="contact-line">www.fernhalehome.com
        <svg viewBox="0 0 10 10"><circle cx="5" cy="5" r="4.6" fill="none" stroke="#6cc12e" stroke-width="1"/><path d="M0.5 5 H9.5 M5 0.5 V9.5" stroke="#6cc12e" stroke-width="0.8"/><ellipse cx="5" cy="5" rx="2" ry="4.6" fill="none" stroke="#6cc12e" stroke-width="0.8"/></svg></p>
    </div>
  </section>
</body>
</html>
```